Harborlight Amusement Collective (HAC)

We need a business card design for Harborlight Amusement Collective. Modern and sleek looking, with all critical information. Open to single or double sided designs, if double sided info needs to be all on one side. The main Logo is Harborlight Amusement collective and must be on the card. The other three logos are for the brands that fall under the group, they might be good on the back.

Industry/Entity Type

Business

```html
<!DOCTYPE html>
<html lang="en">
<head>
<meta charset="utf-8">
<title>Harborlight Amusement Collective – Business Card</title>
<link rel="stylesheet" href="https://fonts.googleapis.com/css2?family=Montserrat:wght@400;500;600&family=Saira+Semi+Condensed:wght@600&display=swap">
<style>
  :root {
    --brand-blue: #2a5597;
    --brand-green: #7f9a3a;
    --ink: #232323;
    --card: #f6f6f4;
    --stage: #e7e4e0;
    --band-text: #e9eef7;
  }
  * { margin: 0; padding: 0; box-sizing: border-box; }
  html, body {
    width: 1200px; height: 1054px; overflow: hidden;
    background: var(--stage);
  }
  .card {
    position: absolute; left: 100px; top: 227px;
    width: 1000px; height: 600px;
    background: var(--card);
    box-shadow: 0 6px 24px rgba(0,0,0,.12);
    overflow: hidden;
    font-family: "Montserrat", sans-serif;
    color: var(--ink);
  }
  .brand { position: absolute; left: 61px; top: 75px; display: flex; align-items: center; gap: 56px; }
  .brand-mark { width: 150px; height: 150px; background: var(--brand-blue); }
  .brand-name {
    color: var(--brand-blue); font-weight: 600; text-align: center;
    line-height: 1.25;
  }
  .brand-name .line1 { display: block; font-size: 36px; letter-spacing: 0.5px; }
  .brand-name .line2 { display: block; font-size: 30px; letter-spacing: 10px; margin-top: 14px; }
  .person { position: absolute; left: 62px; top: 436px; }
  .person-name {
    font-family: "Saira Semi Condensed", "Arial Narrow", sans-serif; font-weight: 600;
    font-stretch: semi-condensed;
    font-size: 38px; color: var(--brand-blue); line-height: 1; white-space: nowrap;
  }
  .person-title { font-size: 23px; margin-top: 14px; font-weight: 400; }
  .contact { position: absolute; left: 520px; top: 336px; font-size: 23px; font-weight: 400; }
  .address { line-height: 1.45; }
  .contact-row { display: flex; align-items: center; gap: 22px; margin-top: 10px; }
  .contact-row:first-of-type { margin-top: 24px; }
  .contact-row svg { width: 24px; height: 24px; fill: var(--ink); flex: none; }
  .band { position: absolute; left: 0; top: 0; }
  .website {
    position: absolute; left: 520px; top: 548px;
    font-size: 23px; color: var(--band-text); font-weight: 400;
  }
</style>
</head>
<body>
  <main class="card">
    <div class="brand">
      <div class="brand-mark" aria-hidden="true"></div>
      <div class="brand-name">
        <span class="line1">HARBORLIGHT AMUSEMENT</span>
        <span class="line2">COLLECTIVE</span>
      </div>
    </div>

    <div class="person">
      <div class="person-name">Marlow Deane Ashby</div>
      <div class="person-title">Managing Director</div>
    </div>

    <div class="contact">
      <div class="address">418 Beacon Quay Rd., Port<br>Town, US 204517</div>
      <div class="contact-row">
        <svg viewBox="0 0 24 24" aria-hidden="true"><path d="M3 8c0-2 4-4 9-4s9 2 9 4v2h-5V8.5c-1.3-.5-2.6-.7-4-.7s-2.7.2-4 .7V10H3z"/><path d="M6 11l2-2h8l2 2v9H6z"/><circle cx="12" cy="15" r="2" fill="#f6f6f4"/></svg>
        <span>310.482.7160</span>
      </div>
      <div class="contact-row">
        <svg viewBox="0 0 24 24" aria-hidden="true"><path d="M3 6h18v12H3z"/><path d="M3 6l9 7 9-7" fill="none" stroke="#f6f6f4" stroke-width="1.6"/></svg>
        <span>mdeane@harborlightac.com</span>
      </div>
    </div>

    <svg class="band" width="1000" height="600" viewBox="0 0 1000 600" aria-hidden="true">
      <rect x="0" y="577" width="420" height="23" fill="var(--brand-green)"/>
      <path d="M445 527 H1000 V600 H385 C405 575 420 540 445 527 Z" fill="var(--brand-blue)"/>
    </svg>
    <div class="website">www.harborlightac.com</div>
  </main>
</body>
</html>
```